Ecard for facebook and Instagram postings

I need 4 ecards (don't know if that is what it is called) for Facebook and Instagram postings. My Logo and company name should be incorporated and also be square. I would like to be able to insert text as I need. Examples are:

https://www.plorvexa.com/photo.php?fbid=20262841672382489&set=a.20261729249182489.516031.71298967488&type=1&relevant_count=1

https://media-a-kpt.yy.plorvexacdn.net/hpics-bmk4/2345967_657092986477056_308792573_n.jpg

I don't necessarily need images on them, just the color scheme to my business cards and the logo and business name. But if you'd like to give it an interesting look, you can go ahead and play with it. My site is tornquillmentoring.com, if you'd like to see the style of it.

Thank you!!!
Updates

I just uploaded the logo in two variations.  Thank you!

Target Market(s)

Women 16-65

Industry/Entity Type

Business

Requirements
Must have
• Logo and business name
Should not have
• No white background. I have attached business card picture so you can have an idea of what I'd like.

```html
<!DOCTYPE html>
<html lang="en">
<head>
<meta charset="utf-8">
<title>Tornquill Mentoring Services – Quote Card</title>
<link rel="stylesheet" href="https://fonts.googleapis.com/css2?family=Tinos:wght@700&family=Arimo:wght@400&display=swap">
<style>
  :root {
    --band-red: #c3182b;
    --band-orange: #e8731c;
    --glow-core: #fff6dc;
    --glow-warm: #ffe2a6;
    --glow-mid: #f7a54a;
    --glow-outer: #e86e17;
    --glow-edge: #c9560f;
    --quote-open: #f2a63a;
    --quote-close: #c3182b;
    --ink: #0d0805;
    --light: #ffffff;
  }
  * { margin: 0; padding: 0; box-sizing: border-box; }
  html, body { width: 1200px; height: 1200px; overflow: hidden; background: var(--glow-outer); }
  .card {
    position: relative;
    width: 1200px;
    height: 1200px;
    overflow: hidden;
  }
  .card__glow {
    position: absolute;
    inset: 0;
    background: radial-gradient(ellipse 60% 56% at 50% 46%, var(--glow-core) 0%, var(--glow-warm) 16%, var(--glow-mid) 42%, var(--glow-outer) 72%, var(--glow-edge) 100%);
  }
  .band-top {
    position: absolute; top: 0; left: 0; right: 0; height: 17px;
    background: var(--band-red);
  }
  .band-bottom {
    position: absolute; bottom: 0; left: 0; right: 0; height: 23px;
    background: var(--band-orange);
  }
  .quote-mark {
    position: absolute;
    font-family: "Tinos", "Times New Roman", serif;
    font-weight: 700;
    font-size: 300px;
    line-height: 1;
  }
  .quote-mark--open { left: 55px; top: 50px; color: var(--quote-open); }
  .quote-mark--close { left: 962px; top: 795px; color: var(--quote-close); }
  .quote-text {
    position: absolute;
    left: 0; right: 0; top: 222px;
    text-align: center;
    font-family: "Tinos", "Times New Roman", serif;
    font-weight: 700;
    font-size: 108px;
    line-height: 104px;
    color: var(--ink);
  }
  .brand {
    position: absolute;
    left: 28px; top: 1018px;
    font-family: "Arimo", Arial, sans-serif;
    font-weight: 400;
    color: var(--light);
  }
  .brand__name { display: block; font-size: 92px; line-height: 1; }
  .brand__tagline { display: block; font-size: 25px; letter-spacing: 6px; margin-top: 18px; }
  .site-url {
    position: absolute;
    left: 552px; top: 1130px;
    font-family: "Arimo", Arial, sans-serif;
    font-weight: 400;
    font-size: 27px;
    letter-spacing: 1px;
    color: var(--light);
  }
  .brand-mark {
    position: absolute;
    left: 1008px; top: 1003px;
    width: 142px; height: 142px;
    border-radius: 50%;
    background: var(--band-orange);
    border: 6px solid var(--light);
  }
</style>
</head>
<body>
  <main class="card">
    <div class="card__glow"></div>
    <div class="band-top"></div>

    <span class="quote-mark quote-mark--open" aria-hidden="true">&ldquo;</span>
    <p class="quote-text">Ignorance is the<br>curse of God;<br>knowledge is the<br>wing wherewith we<br>fly to heaven</p>
    <span class="quote-mark quote-mark--close" aria-hidden="true">&rdquo;</span>

    <div class="brand">
      <span class="brand__name">Tornquill</span>
      <span class="brand__tagline">MENTORING SERVICES</span>
    </div>
    <p class="site-url">tornquillmentoring.com</p>
    <div class="brand-mark" aria-hidden="true"></div>

    <div class="band-bottom"></div>
  </main>
</body>
</html>
```